Halvorsen Ridge Consulting Needs a Letterhead

Tomi, we need a letterhead/banner for our blog, which is titled "Marigold Crossroads". The letterhead/banner should incorporate the enclosed banner image, logo, and the name of our blog ("Marigold Crossroads").

We would also like an alternative design that includes our picture. Here, we have two options that we would like to see.

In all, we would like to see 3 different designs: one banner without any pics; and two banner with two versions of our pictures.

The file size should be able to be resized for the space given to us at our website (http://halvorsen-ridge-consulting.com).

We also need the letterhead/banner by Friday, June 13. Thanks!!

```html
<!DOCTYPE html>
<html lang="en">
<head>
<meta charset="utf-8">
<title>Marigold Crossroads — Halvorsen Ridge Consulting</title>
<link rel="stylesheet" href="https://fonts.googleapis.com/css2?family=Arimo:wght@400&display=swap">
<style>
  :root {
    --banner-bg: #000000;
    --title-gold: #c9b76c;
    --panel-bg: #221e1e;
    --brand-text: #e6dc8e;
  }
  html, body {
    margin: 0;
    padding: 0;
    width: 1200px;
    height: 250px;
    overflow: hidden;
    background: var(--banner-bg);
  }
  .banner {
    position: relative;
    width: 1200px;
    height: 250px;
    background: var(--banner-bg);
    font-family: "Arimo", Arial, sans-serif;
  }
  .blog-title {
    position: absolute;
    left: 20px;
    top: 12px;
    margin: 0;
    font-weight: 400;
    font-size: 81px;
    line-height: 106px;
    color: var(--title-gold);
    letter-spacing: -0.5px;
  }
  .blog-title span {
    display: block;
  }
  .brand-panel {
    position: absolute;
    left: 875px;
    top: 28px;
    width: 297px;
    height: 197px;
    background: var(--panel-bg);
  }
  .brand-name {
    position: absolute;
    left: 0;
    right: 0;
    bottom: 22px;
    margin: 0;
    text-align: center;
    font-weight: 400;
    font-size: 20px;
    line-height: 24px;
    color: var(--brand-text);
  }
</style>
</head>
<body>
  <header class="banner">
    <h1 class="blog-title">
      <span>Marigold</span>
      <span>Crossroads</span>
    </h1>
    <div class="brand-panel">
      <p class="brand-name">Halvorsen Ridge<br>Consulting</p>
    </div>
  </header>
</body>
</html>
```